Web design project for exciting Australian start-up

Background
We are looking for a creative and talented web design artist to work alongside our market leading web developer.
• You will be required to create a modern and clean design theme for our website, incorporating selected rustic colour scheme elements for our exciting Australian start-up to operate within the coffee industry.
reoccurring work to be expected to flow to the successful designer.
Requirements
• c. 5 - 10 page website
• Landing page
• Log in/ out
• 404 template
• Typography is emphasised
• Please use either a) typemarrow.com, b) free web fonts, c) brindle fonts
• All design elements in vector format
• Preferably with icons for each header title(i.e. about us, how it works etc) but designer have free reign over how the site looks, so might not be applicable
• All pages to be responsive
• Down to eSlab resolution

High level visual design brief attached - additional pages to be worked from base design.

Design inspiration
• We would like to use design elements from the following sources:
http://www.zandrix.com/halcyon/ (Functionality)
Colour scheme refer to logo and complementary style guide

```html
<!DOCTYPE html>
<html lang="en">
<head>
<meta charset="utf-8">
<title>Bean Harbour – Marketplace</title>
<link rel="stylesheet" href="https://fonts.googleapis.com/css2?family=Oswald:wght@400;500;600&family=Lato:wght@400;700&display=swap">
<style>
  :root {
    --orange: #ef8a14;
    --btn-top: #f1a14c;
    --btn-bottom: #e48624;
    --ink: #1d1d1d;
    --text: #2b2b2b;
    --page: #f7f7f7;
    --card: #ffffff;
    --line: #d6d6d6;
    --star: #e1a623;
    --star-off: #d8d8d8;
    --white: #ffffff;
  }
  * { box-sizing: border-box; margin: 0; padding: 0; }
  html, body { width: 1200px; height: 1093px; overflow: hidden; }
  body {
    position: relative;
    background: var(--page);
    font-family: "Lato", Arial, sans-serif;
    color: var(--text);
  }
  a { color: inherit; text-decoration: none; }

  /* Header */
  .site-header {
    position: absolute; left: 0; top: 66px; width: 1200px; height: 48px;
    background: linear-gradient(180deg, #f39a2c 0%, #ee8410 100%);
    box-shadow: 0 3px 6px rgba(0,0,0,0.2);
  }
  .brand {
    position: absolute; left: 0; top: 0; width: 1200px; height: 48px;
    display: flex; align-items: center; justify-content: center; gap: 10px;
  }
  .brand-dot {
    width: 14px; height: 14px; border-radius: 50%;
    background: var(--white);
  }
  .brand-name {
    font-family: "Lato", Arial, sans-serif; font-weight: 700;
    font-size: 24px; color: var(--white);
  }
  .account-nav {
    position: absolute; right: 92px; top: 0; height: 48px;
    display: flex; align-items: center;
    font-family: "Oswald", Arial, sans-serif; font-size: 17px; color: var(--white);
  }
  .account-nav a { padding: 0 12px; line-height: 36px; }
  .account-nav a + a { border-left: 1px solid rgba(120,60,0,0.6); }

  /* Main */
  .section-title {
    position: absolute; left: 73px;
    font-family: "Oswald", Arial, sans-serif; font-weight: 500;
    font-size: 20px; color: var(--orange);
  }
  .filter-btn {
    position: absolute; top: 218px; height: 39px;
    border-radius: 4px;
    background: linear-gradient(180deg, var(--btn-top), var(--btn-bottom));
    color: var(--white); font-weight: 700; font-size: 15px;
    display: flex; align-items: center; justify-content: center;
  }
  .search-bar {
    position: absolute; left: 73px; top: 298px; width: 1054px; height: 30px;
    display: flex; align-items: center; font-size: 15px; color: var(--ink);
  }
  .save-star { margin-left: 18px; margin-right: 14px; width: 18px; height: 18px; }
  .sort-label { position: absolute; left: 752px; }
  .sort-select {
    position: absolute; left: 806px; top: -1px; width: 128px; height: 32px;
    border: 1px solid var(--line); border-radius: 4px; background: var(--white);
    font-size: 13px; padding-left: 12px; display: flex; align-items: center;
  }
  .sort-select svg { position: absolute; right: 10px; top: 11px; }
  .view-label { position: absolute; left: 966px; }
  .view-icons { position: absolute; left: 1014px; top: 8px; display: flex; gap: 8px; }
  .divider { position: absolute; left: 73px; top: 343px; width: 1054px; height: 1px; background: var(--line); }

  /* Result cards */
  .bean-card {
    position: absolute; left: 73px; width: 1054px; height: 132px;
    background: var(--card); border: 1px solid #e3e3e3;
  }
  .bean-photo { position: absolute; left: 15px; top: 16px; width: 98px; height: 91px; }
  .bean-title { position: absolute; left: 132px; top: 12px; font-size: 15px; font-weight: 700; color: var(--orange); }
  .bean-blend { position: absolute; left: 132px; top: 38px; font-size: 15px; font-weight: 700; color: var(--text); }
  .bean-specs { position: absolute; left: 171px; top: 72px; font-size: 12.5px; line-height: 20px; color: var(--ink); list-style: none; }
  .review-icon { position: absolute; left: 745px; top: 10px; }
  .review-title { position: absolute; right: 9px; top: 18px; font-size: 19px; font-weight: 700; color: var(--orange); }
  .rating { position: absolute; left: 806px; top: 50px; display: flex; align-items: center; }
  .rating svg { margin-right: 4px; }
  .rating-label { margin-left: 6px; font-size: 10px; line-height: 19px; font-weight: 700; color: var(--ink); width: 90px; }
  .offer-icons { position: absolute; left: 797px; top: 101px; display: flex; gap: 12px; align-items: center; }
  .offer-link { position: absolute; right: 9px; top: 102px; font-size: 15px; font-weight: 700; color: var(--orange); }

  /* Footer */
  .site-footer {
    position: absolute; left: 0; top: 813px; width: 1200px; height: 280px;
    background: linear-gradient(180deg, #f08a0e 0%, #e39a52 100%);
    color: var(--white);
  }
  .footer-col { position: absolute; top: 40px; }
  .footer-col h2 { font-family: "Oswald", Arial, sans-serif; font-weight: 500; font-size: 20px; margin-bottom: 14px; }
  .footer-col ul { list-style: none; }
  .footer-col li { font-size: 15px; line-height: 33px; }
  .footer-col.right { right: 71px; text-align: right; }
  .footer-col.right li { text-align: left; }
  .copyright {
    position: absolute; left: 71px; top: 246px;
    font-family: "Oswald", Arial, sans-serif; font-size: 16px; letter-spacing: 0.3px;
  }
</style>
</head>
<body>

<header class="site-header">
  <div class="brand">
    <span class="brand-dot"></span>
    <span class="brand-name">Bean Harbour</span>
  </div>
  <nav class="account-nav">
    <a href="#">Login</a>
    <a href="#">Sign up</a>
  </nav>
</header>

<main>
  <h1 class="section-title" style="top:164px">Marketplace</h1>

  <a class="filter-btn" href="#" style="left:73px;width:163px">Tender format</a>
  <a class="filter-btn" href="#" style="left:241px;width:97px">All</a>
  <a class="filter-btn" href="#" style="left:344px;width:98px">One-off</a>
  <a class="filter-btn" href="#" style="left:447px;width:99px">Recurring</a>
  <a class="filter-btn" href="#" style="left:876px;width:121px">Quantity (kg)</a>
  <a class="filter-btn" href="#" style="left:1007px;width:119px">35 kg/week</a>

  <div class="search-bar">
    <span>[X] results for Café Morsel</span>
    <svg class="save-star" viewBox="0 0 24 24"><path d="M12 2l3 7 7 .6-5.4 4.7 1.7 7.2L12 17.7 5.7 21.5l1.7-7.2L2 9.6 9 9z" fill="var(--star)"/></svg>
    <span>Save search</span>
    <span class="sort-label">Sort</span>
    <div class="sort-select">Highest rated
      <svg width="12" height="8" viewBox="0 0 12 8"><path d="M1 1l5 5 5-5" fill="none" stroke="#aaa" stroke-width="1.5"/></svg>
    </div>
    <span class="view-label">View</span>
    <div class="view-icons">
      <svg width="16" height="14" viewBox="0 0 16 14" fill="#bbb"><rect x="0" y="0" width="4" height="3"/><rect x="6" y="0" width="4" height="3"/><rect x="12" y="0" width="4" height="3"/><rect x="0" y="5" width="4" height="3"/><rect x="6" y="5" width="4" height="3"/><rect x="12" y="5" width="4" height="3"/><rect x="0" y="10" width="4" height="3"/><rect x="6" y="10" width="4" height="3"/><rect x="12" y="10" width="4" height="3"/></svg>
      <svg width="16" height="14" viewBox="0 0 16 14" fill="#bbb"><rect x="0" y="0" width="4" height="3"/><rect x="6" y="0" width="10" height="3"/><rect x="0" y="5" width="4" height="3"/><rect x="6" y="5" width="10" height="3"/><rect x="0" y="10" width="4" height="3"/><rect x="6" y="10" width="10" height="3"/></svg>
    </div>
  </div>
  <div class="divider"></div>

  <h2 class="section-title" style="top:370px">Result</h2>

  <article class="bean-card" style="top:443px">
    <div class="bean-photo" role="img" aria-label="Photo of a white coffee cup on a saucer among roasted beans" style="background:linear-gradient(160deg,#6b2c12 0%,#3a1608 60%,#1e0c05 100%)"></div>
    <h3 class="bean-title">Coffee bean XX</h3>
    <p class="bean-blend">Blend description:</p>
    <ul class="bean-specs"><li>Origin [xx]</li><li>Grind availability [xx]</li></ul>
    <svg class="review-icon" width="52" height="50" viewBox="0 0 52 50"><path d="M26 3C13 3 3 11 3 22s10 19 23 19c4 0 7-.6 10-1.8L48 46l-4-10c4-3.5 6-8.5 6-14C50 11 39 3 26 3z" fill="none" stroke="var(--star)" stroke-width="2.5"/></svg>
    <h4 class="review-title">Reviews for this bean</h4>
    <div class="rating">
      <svg width="21" height="20" viewBox="0 0 24 24"><path d="M12 2l3 7 7 .6-5.4 4.7 1.7 7.2L12 17.7 5.7 21.5l1.7-7.2L2 9.6 9 9z" fill="var(--star)"/></svg>
      <svg width="21" height="20" viewBox="0 0 24 24"><path d="M12 2l3 7 7 .6-5.4 4.7 1.7 7.2L12 17.7 5.7 21.5l1.7-7.2L2 9.6 9 9z" fill="var(--star)"/></svg>
      <svg width="21" height="20" viewBox="0 0 24 24"><path d="M12 2l3 7 7 .6-5.4 4.7 1.7 7.2L12 17.7 5.7 21.5l1.7-7.2L2 9.6 9 9z" fill="var(--star)"/></svg>
      <svg width="21" height="20" viewBox="0 0 24 24"><path d="M12 2l3 7 7 .6-5.4 4.7 1.7 7.2L12 17.7 5.7 21.5l1.7-7.2L2 9.6 9 9z" fill="var(--star-off)"/></svg>
      <svg width="21" height="20" viewBox="0 0 24 24"><path d="M12 2l3 7 7 .6-5.4 4.7 1.7 7.2L12 17.7 5.7 21.5l1.7-7.2L2 9.6 9 9z" fill="var(--star-off)"/></svg>
      <span class="rating-label">Wholesaler's overall customer rating</span>
    </div>
    <div class="offer-icons">
      <svg width="16" height="16" viewBox="0 0 16 16"><rect x="2" y="2" width="11" height="11" fill="none" stroke="var(--ink)" stroke-width="2"/><rect x="5" y="5" width="5" height="5" fill="var(--ink)"/></svg>
      <svg width="30" height="22" viewBox="0 0 30 22"><path d="M2 8l13-6 13 6-13 6z" fill="none" stroke="var(--ink)" stroke-width="1.8"/><path d="M7 11v6c4 3 12 3 16 0v-6" fill="none" stroke="var(--ink)" stroke-width="1.8"/><path d="M4 9v8" stroke="var(--ink)" stroke-width="1.8"/></svg>
      <svg width="14" height="22" viewBox="0 0 14 22"><rect x="1" y="1" width="12" height="4" fill="var(--ink)"/><path d="M2 6h10l-1.5 15h-7z" fill="var(--ink)"/><rect x="3" y="10" width="8" height="4" fill="var(--white)"/></svg>
      <svg width="24" height="20" viewBox="0 0 24 20"><path d="M2 8h5l11-6v16L7 12H2z" fill="var(--ink)"/><path d="M6 12l2 6h3l-2-6" fill="var(--ink)"/></svg>
    </div>
    <a class="offer-link" href="#">Other offerings</a>
  </article>

  <article class="bean-card" style="top:632px">
    <div class="bean-photo" role="img" aria-label="Photo of a steaming cup of black coffee on a dark table" style="background:linear-gradient(160deg,#2a1108 0%,#7a3410 55%,#c07020 100%)"></div>
    <h3 class="bean-title">Coffee bean XX</h3>
    <p class="bean-blend">Blend description:</p>
    <ul class="bean-specs"><li>Origin [xx]</li><li>Grind availability [xx]</li></ul>
    <svg class="review-icon" width="52" height="50" viewBox="0 0 52 50"><path d="M26 3C13 3 3 11 3 22s10 19 23 19c4 0 7-.6 10-1.8L48 46l-4-10c4-3.5 6-8.5 6-14C50 11 39 3 26 3z" fill="none" stroke="var(--star)" stroke-width="2.5"/></svg>
    <h4 class="review-title">Reviews for this bean</h4>
    <div class="rating">
      <svg width="21" height="20" viewBox="0 0 24 24"><path d="M12 2l3 7 7 .6-5.4 4.7 1.7 7.2L12 17.7 5.7 21.5l1.7-7.2L2 9.6 9 9z" fill="var(--star)"/></svg>
      <svg width="21" height="20" viewBox="0 0 24 24"><path d="M12 2l3 7 7 .6-5.4 4.7 1.7 7.2L12 17.7 5.7 21.5l1.7-7.2L2 9.6 9 9z" fill="var(--star)"/></svg>
      <svg width="21" height="20" viewBox="0 0 24 24"><path d="M12 2l3 7 7 .6-5.4 4.7 1.7 7.2L12 17.7 5.7 21.5l1.7-7.2L2 9.6 9 9z" fill="var(--star)"/></svg>
      <svg width="21" height="20" viewBox="0 0 24 24"><path d="M12 2l3 7 7 .6-5.4 4.7 1.7 7.2L12 17.7 5.7 21.5l1.7-7.2L2 9.6 9 9z" fill="var(--star-off)"/></svg>
      <svg width="21" height="20" viewBox="0 0 24 24"><path d="M12 2l3 7 7 .6-5.4 4.7 1.7 7.2L12 17.7 5.7 21.5l1.7-7.2L2 9.6 9 9z" fill="var(--star-off)"/></svg>
      <span class="rating-label">Wholesaler's overall customer rating</span>
    </div>
    <div class="offer-icons">
      <svg width="16" height="16" viewBox="0 0 16 16"><rect x="2" y="2" width="11" height="11" fill="none" stroke="var(--ink)" stroke-width="2"/><rect x="5" y="5" width="5" height="5" fill="var(--ink)"/></svg>
      <svg width="30" height="22" viewBox="0 0 30 22"><path d="M2 8l13-6 13 6-13 6z" fill="none" stroke="var(--ink)" stroke-width="1.8"/><path d="M7 11v6c4 3 12 3 16 0v-6" fill="none" stroke="var(--ink)" stroke-width="1.8"/><path d="M4 9v8" stroke="var(--ink)" stroke-width="1.8"/></svg>
      <svg width="14" height="22" viewBox="0 0 14 22"><rect x="1" y="1" width="12" height="4" fill="var(--ink)"/><path d="M2 6h10l-1.5 15h-7z" fill="var(--ink)"/><rect x="3" y="10" width="8" height="4" fill="var(--white)"/></svg>
      <svg width="24" height="20" viewBox="0 0 24 20"><path d="M2 8h5l11-6v16L7 12H2z" fill="var(--ink)"/><path d="M6 12l2 6h3l-2-6" fill="var(--ink)"/></svg>
    </div>
    <a class="offer-link" href="#">Other offerings</a>
  </article>
</main>

<footer class="site-footer">
  <div class="footer-col" style="left:71px">
    <h2>Helpful info</h2>
    <ul><li>About us</li><li>Media enquiries</li><li>Terms &amp; conditions</li><li>Privacy policy</li></ul>
  </div>
  <div class="footer-col" style="left:423px">
    <h2>Who we are</h2>
    <ul><li>How it works</li><li>FAQ</li><li>Contact us</li></ul>
  </div>
  <div class="footer-col right">
    <h2>Join us on</h2>
    <ul><li>Facefold</li><li>Chirper</li><li>Linkwork</li><li>ViewReel</li></ul>
  </div>
  <p class="copyright">Copyright © 2014 Bean Harbour</p>
</footer>

</body>
</html>
```